QP Fiduciary Website Redesign Contest

We want to refresh our website to be more insitutional, professional for an international audience. We have designed a new logo for this purpose and that has been attached. A full brand brief and positioning statement has also been attached. Please read through all the documents carefully before designing. The old website is found here: https://qp-fiduciary.example/

Target Market(s)

Actuaries and associated businesses internationally

Industry/Entity Type

professional services - actuaries

Number of Pages Required

3 page

Font styles to use
Sans Serif

Colors
0054AA
0677BA
7BADD7
CADEEF
E8F1F8
0094D4
00A9DD
6FCCEA
C7EBF8
E9F6FB
F0912C
F2A743
F7CA91
FBE8D2
FDF5EE
EE7325
F08F49
F5BC92
FAE3D3
FDF4ED
EB3D1F
EC4F4E
F09395
F8D3D4
FCEDEE

Requirements
Must have
• blues and greens to match the logo color, complimentary colors, navigation
Nice to have
• old site: https://qp-fiduciary.example/

```html
<!DOCTYPE html>
<html lang="en">
<head>
<meta charset="utf-8">
<title>QP Fiduciary — Actuarial Software</title>
<link rel="stylesheet" href="https://fonts.googleapis.com/css2?family=Archivo:wght@600;700;800&family=Inter:wght@400;500;600;700&display=swap">
<style>
:root{
  --blue:#0054AA;
  --blue-mid:#0677BA;
  --sky:#0094D4;
  --cyan:#00A9DD;
  --blue-soft:#7BADD7;
  --blue-pale:#CADEEF;
  --blue-wash:#E8F1F8;
  --sky-wash:#E9F6FB;
  --orange:#EE7325;
  --orange-pale:#FAE3D3;
  --ink:#111111;
  --text:#444444;
  --white:#FFFFFF;
  --footer:#0B2A4A;
  --footer-line:#2A4A6E;
}
*{box-sizing:border-box;margin:0;padding:0}
html,body{width:1200px;height:4098px;overflow:hidden}
body{position:relative;background:var(--white);font-family:"Inter",Arial,sans-serif;color:var(--text)}
.abs{position:absolute}
.brand{font-family:"Archivo",Arial,sans-serif;font-weight:700;color:var(--ink);letter-spacing:1px;display:flex;align-items:center;gap:10px}
.brand-dot{width:14px;height:14px;border-radius:50%;background:var(--sky)}
.btn{position:absolute;display:flex;align-items:center;justify-content:center;gap:12px;background:var(--blue);color:#fff;border-radius:30px;font-weight:500;font-family:"Inter",Arial,sans-serif}
.btn .arrow{width:30px;height:30px;border-radius:50%;background:#fff;display:flex;align-items:center;justify-content:center}
.section-title{position:absolute;left:0;width:1200px;text-align:center;font-family:"Archivo",Arial,sans-serif;font-weight:700;font-size:35px;color:var(--ink);letter-spacing:.5px}
.section-title span{color:var(--sky)}
.title-rule{position:absolute;left:577px;width:46px;height:2px;background:var(--orange)}
.section-sub{position:absolute;left:0;width:1200px;text-align:center;font-size:14px;color:var(--text);line-height:23px}

/* header */
.site-header{top:0;left:0;width:1200px;height:70px;background:#fff}
.site-header .brand{position:absolute;left:70px;top:20px;font-size:28px}
.main-nav{position:absolute;top:27px;left:390px;font-size:13px;color:var(--ink)}
.main-nav a{position:absolute;white-space:nowrap;text-decoration:none;color:var(--ink)}
.main-nav a.active{color:var(--blue)}

/* hero */
.hero{top:70px;left:0;width:1200px;height:544px;background:linear-gradient(90deg,#0d1f33 0%,#1e3a58 35%,#5a7590 60%,#a3b4c4 85%,#7f93a6 100%)}
.hero-shade{top:0;left:0;width:700px;height:544px;background:linear-gradient(90deg,rgba(0,10,25,.55),rgba(0,0,0,0))}
.hero h1{position:absolute;left:70px;top:114px;font-family:"Archivo",Arial,sans-serif;font-weight:700;font-size:36px;line-height:46px;color:#fff;letter-spacing:.5px}
.hero p{position:absolute;left:71px;top:308px;font-size:13.5px;line-height:23px;color:#fff}
.hero p b{font-weight:700}

/* overview cards */
.feature-card{position:absolute;top:826px;width:214px;height:256px;background:#fff;border-radius:8px;box-shadow:0 2px 14px rgba(0,40,90,.08)}
.feature-card svg{position:absolute;left:22px;top:30px}
.feature-card h3{position:absolute;left:22px;top:102px;width:180px;font-size:15px;font-weight:600;color:var(--ink);line-height:20px}
.feature-card .rule{position:absolute;left:22px;top:152px;width:30px;height:2px;background:var(--orange)}
.feature-card p{position:absolute;left:22px;top:170px;width:170px;font-size:12px;line-height:19px;color:var(--text)}

/* solutions */
.band-tint{left:0;width:1200px;background:var(--blue-wash)}
.photo{border-radius:10px}
.solution{position:absolute;left:629px;width:440px}
.solution .icon{position:absolute;left:0;top:0;width:71px;height:71px;border-radius:50%;display:flex;align-items:center;justify-content:center}
.solution h3{position:absolute;left:92px;top:0;font-size:15px;font-weight:600;color:var(--ink)}
.solution p{position:absolute;left:92px;top:24px;width:335px;font-size:12px;line-height:19px;color:var(--text)}
.learn{font-size:12px;color:var(--blue);display:flex;align-items:center;gap:10px;position:absolute}

/* characteristics */
.char-icon{position:absolute;width:80px;height:80px;border-radius:50%;display:flex;align-items:center;justify-content:center}
.char-text{position:absolute;width:270px}
.char-text h3{font-size:15px;font-weight:600;color:var(--ink);margin-bottom:6px}
.char-text p{font-size:12px;line-height:19px;color:var(--text)}
.char-text.left{text-align:right}

/* insights */
.insight{position:absolute;top:2728px;width:286px;height:368px;background:#fff;border-radius:8px;overflow:hidden;box-shadow:0 2px 12px rgba(0,40,90,.06)}
.insight .thumb{height:191px}
.insight h3{position:absolute;left:19px;top:204px;width:255px;font-size:15px;font-weight:600;color:var(--ink);line-height:21px}
.insight p{position:absolute;left:19px;top:256px;width:250px;font-size:12px;line-height:19px;color:var(--text)}

/* cta */
.cta{left:142px;top:3345px;width:916px;height:376px;border-radius:18px;overflow:hidden;background:radial-gradient(circle at 28% 25%,#1f5f96 0%,#123b63 30%,#0a2340 65%,#06162a 100%)}
.cta h2{position:absolute;left:0;top:78px;width:916px;text-align:center;font-family:"Archivo",Arial,sans-serif;font-weight:700;font-size:35px;line-height:44px;color:#fff;letter-spacing:.5px}
.cta p{position:absolute;left:0;top:178px;width:916px;text-align:center;font-size:14px;line-height:23px;color:#fff}

/* footer */
.site-footer{left:0;top:3614px;width:1200px;height:484px;background:var(--footer);color:#e0e8f0}
.site-footer .brand{position:absolute;left:142px;top:190px;font-size:34px;color:#fff}
.footer-about{position:absolute;left:142px;top:260px;width:300px;font-size:12px;line-height:19px;color:#d8e2ec}
.footer-h{position:absolute;top:202px;font-family:"Archivo",Arial,sans-serif;font-weight:600;font-size:16px;color:#fff;letter-spacing:.5px}
.quick-links{position:absolute;left:576px;top:248px;list-style:none;font-size:12px;color:#d8e2ec}
.quick-links li{height:28px}
.contact-row{position:absolute;left:813px;display:flex;gap:14px;font-size:12px;line-height:19px;color:#d8e2ec}
.contact-row strong{color:#fff;font-weight:600;font-size:13px}
.footer-rule{position:absolute;left:142px;top:433px;width:916px;height:1px;background:var(--footer-line)}
.copyright{position:absolute;left:142px;top:452px;font-size:12px;color:#d8e2ec}
.social{position:absolute;top:446px;width:32px;height:32px;border-radius:50%;background:#fff}
</style>
</head>
<body>

<!-- Header -->
<header class="abs site-header">
  <div class="brand"><span class="brand-dot"></span>QP FIDUCIARY</div>
  <nav class="main-nav">
    <a class="active" style="left:0">Home</a>
    <a style="left:70px">Platform</a>
    <a style="left:154px">Solutions</a>
    <a style="left:241px">Insights</a>
    <a style="left:322px">Company</a>
    <a style="left:412px">Contact</a>
  </nav>
  <div class="btn" style="left:882px;top:16px;width:248px;height:38px;font-size:13px">Request a Technical Walkthrough</div>
</header>

<!-- Hero -->
<section class="abs hero" role="img" aria-label="Photo of two professionals shaking hands in a bright modern office">
  <div class="abs hero-shade"></div>
  <h1>ACTUARIAL SOFTWARE<br>FOR STRUCTURED,<br>AUDITABLE FINANCIAL<br>ANALYSIS.</h1>
  <p><b>QP Fiduciary</b> develops software that translates established<br>actuarial methodologies into disciplined, decision-ready tools.</p>
  <div class="btn" style="left:70px;top:374px;width:304px;height:45px;font-size:14px;justify-content:flex-start;padding-left:24px">Request A Technical Walkthrough
    <span class="arrow" style="position:absolute;right:8px"><svg width="14" height="14" viewBox="0 0 14 14"><path d="M2 7h10M8 3l4 4-4 4" fill="none" stroke="#0054AA" stroke-width="1.6"/></svg></span></div>
</section>

<!-- Platform overview -->
<h2 class="section-title" style="top:682px">PLATFORM <span>OVERVIEW</span></h2>
<div class="title-rule" style="top:735px"></div>
<p class="section-sub" style="top:754px">Our platform empowers actuaries and risk professionals with tools designed for modern<br>regulatory and business demands.</p>

<div class="feature-card" style="left:142px">
  <svg width="52" height="52" viewBox="0 0 52 52" fill="none" stroke="#0054AA" stroke-width="1.5"><circle cx="34" cy="34" r="14" fill="#E8F1F8" stroke="none"/><rect x="4" y="18" width="40" height="26" rx="2"/><circle cx="24" cy="8" r="4"/><path d="M24 12v8M12 30h24M12 30v6M24 30v6M36 30v6"/></svg>
  <h3>Structured Workflows</h3><div class="rule"></div>
  <p>that guide users through every step of the analysis process</p>
</div>
<div class="feature-card" style="left:376px">
  <svg width="52" height="52" viewBox="0 0 52 52" fill="none" stroke="#0094D4" stroke-width="1.5"><circle cx="30" cy="22" r="18" fill="#E9F6FB" stroke="none"/><circle cx="22" cy="24" r="16"/><path d="M10 30l20-20M14 36l22-22M20 38l18-18"/></svg>
  <h3>Full Transparency Of Assumptions</h3><div class="rule"></div>
  <p>that guide users through every step of the analysis process</p>
</div>
<div class="feature-card" style="left:610px">
  <svg width="52" height="52" viewBox="0 0 52 52" fill="none" stroke="#0054AA" stroke-width="1.5"><circle cx="34" cy="30" r="14" fill="#E8F1F8" stroke="none"/><rect x="10" y="6" width="24" height="34" rx="2"/><path d="M15 14h14M15 20h14M15 26h8"/><circle cx="32" cy="32" r="8"/><path d="M38 38l8 8"/></svg>
  <h3>Built-in Auditability</h3><div class="rule"></div>
  <p>that guide users through every step of the analysis process</p>
</div>
<div class="feature-card" style="left:844px">
  <svg width="52" height="52" viewBox="0 0 52 52" fill="none" stroke="#0094D4" stroke-width="1.5"><circle cx="30" cy="26" r="18" fill="#E9F6FB" stroke="none"/><circle cx="24" cy="24" r="18" stroke-dasharray="3 3"/><circle cx="24" cy="24" r="12"/><path d="M16 22h16M18 22v8M22 22v8M26 22v8M30 22v8M16 31h16M24 16l-8 5h16z"/></svg>
  <h3>Robust Governance Features</h3><div class="rule"></div>
  <p>that guide users through every step of the analysis process</p>
</div>

<!-- Core solutions -->
<section class="abs band-tint" style="top:1167px;height:682px"></section>
<h2 class="section-title" style="top:1234px">CORE <span>SOLUTIONS</span></h2>
<div class="title-rule" style="top:1287px"></div>
<p class="section-sub" style="top:1307px">Precision-built modules for the most demanding actuarial tasks</p>
<div class="abs photo" style="left:142px;top:1364px;width:423px;height:400px;background:linear-gradient(135deg,#eef3f8 0%,#c9d6e3 45%,#2e3f52 75%,#1a2634 100%)" role="img" aria-label="Photo of two hands joining puzzle pieces"></div>

<div class="solution" style="top:1370px;height:120px">
  <div class="icon" style="background:var(--blue)"><svg width="36" height="36" viewBox="0 0 36 36" fill="none" stroke="#fff" stroke-width="1.5"><circle cx="20" cy="13" r="8"/><path d="M20 5v8h8"/><path d="M4 28l6-4h8l8-3v4l-10 6H4z"/></svg></div>
  <h3>Reserving &amp; Valuation</h3>
  <p>Perform compliant, repeatable reserving and valuation processes with full traceability and support for multiple actuarial methods and regulatory frameworks.</p>
  <div class="learn" style="left:92px;top:92px">Learn More <svg width="16" height="10" viewBox="0 0 16 10"><path d="M1 5h13M10 1l4 4-4 4" fill="none" stroke="#EE7325" stroke-width="1.4"/></svg></div>
</div>
<div class="solution" style="top:1518px;height:120px">
  <div class="icon" style="background:var(--sky)"><svg width="36" height="36" viewBox="0 0 36 36" fill="none" stroke="#fff" stroke-width="1.5"><path d="M8 4h14l6 6v22H8z"/><path d="M12 14h10M12 19h8"/><circle cx="24" cy="26" r="7" fill="#0094D4"/><path d="M24 22v8M22 24h3a1.5 1.5 0 010 3h-2a1.5 1.5 0 000 3h3"/></svg></div>
  <h3>Pricing</h3>
  <p>Build and test pricing models with transparent assumptions, scenario testing, and comparative analytics to support profitable product development.</p>
  <div class="learn" style="left:92px;top:92px">Learn More <svg width="16" height="10" viewBox="0 0 16 10"><path d="M1 5h13M10 1l4 4-4 4" fill="none" stroke="#EE7325" stroke-width="1.4"/></svg></div>
</div>
<div class="solution" style="top:1666px;height:120px">
  <div class="icon" style="background:var(--blue)"><svg width="36" height="36" viewBox="0 0 36 36" fill="none" stroke="#fff" stroke-width="1.5"><circle cx="20" cy="14" r="9"/><path d="M20 8v6l4 3"/><path d="M4 30l6-4h8l8-3v4l-10 6H4z"/></svg></div>
  <h3>Enterprise Risk Management</h3>
  <p>Integrate risk metrics, stress testing, and capital modeling in a governed environment to support ORSA, Solvency II, and other ERM requirements.</p>
  <div class="learn" style="left:92px;top:92px">Learn More <svg width="16" height="10" viewBox="0 0 16 10"><path d="M1 5h13M10 1l4 4-4 4" fill="none" stroke="#EE7325" stroke-width="1.4"/></svg></div>
</div>

<!-- Platform characteristics -->
<h2 class="section-title" style="top:1912px">PLATFORM <span>CHARACTERISTICS</span></h2>
<div class="title-rule" style="top:1970px"></div>
<p class="section-sub" style="top:1991px">Engineered for clarity, built to scale across borders</p>

<svg class="abs" style="left:420px;top:2048px" width="360" height="360" viewBox="0 0 360 360"><circle cx="180" cy="180" r="172" fill="none" stroke="#7BADD7" stroke-width="2"/></svg>
<div class="brand abs" style="left:0;width:1200px;top:2210px;justify-content:center;font-size:30px"><span class="brand-dot"></span>QP FIDUCIARY</div>

<div class="char-icon" style="left:442px;top:2073px;background:var(--blue)"><svg width="38" height="38" viewBox="0 0 38 38" fill="none" stroke="#fff" stroke-width="1.5"><rect x="14" y="4" width="10" height="8"/><path d="M19 12v8M7 20h24M7 20v6M19 20v6M31 20v6"/><rect x="3" y="26" width="8" height="7"/><rect x="15" y="26" width="8" height="7"/><rect x="27" y="26" width="8" height="7"/></svg></div>
<div class="char-icon" style="left:678px;top:2073px;background:var(--sky)"><svg width="38" height="38" viewBox="0 0 38 38" fill="none" stroke="#fff" stroke-width="1.5"><circle cx="12" cy="11" r="6"/><circle cx="27" cy="12" r="4"/><path d="M4 32l6-4h9l8-4v4l-10 6H4z"/></svg></div>
<div class="char-icon" style="left:442px;top:2306px;background:var(--sky)"><svg width="38" height="38" viewBox="0 0 38 38" fill="none" stroke="#fff" stroke-width="1.5"><path d="M8 4h16l6 6v24H8z"/><circle cx="19" cy="19" r="6"/><path d="M23 23l6 6M13 10h8"/></svg></div>
<div class="char-icon" style="left:678px;top:2306px;background:var(--blue)"><svg width="38" height="38" viewBox="0 0 38 38" fill="none" stroke="#fff" stroke-width="1.5"><circle cx="19" cy="16" r="10"/><path d="M15 20v-5M19 20v-8M23 20v-3M4 32l8-6 6 3 8-7 8 4"/></svg></div>

<div class="char-text left" style="left:148px;top:2081px"><h3>Structured Workflows</h3><p>Consistent, repeatable processes from<br>data to disclosure.</p></div>
<div class="char-text" style="left:781px;top:2081px"><h3>Multi-jurisdictional Review Support</h3><p>Localise assumptions, outputs, and reports<br>for any regulator.</p></div>
<div class="char-text left" style="left:148px;top:2314px"><h3>Transparent Assumptions</h3><p>Every assumption exposed, documented,<br>and linked to source.</p></div>
<div class="char-text" style="left:781px;top:2314px"><h3>Comparative Analysis Capability</h3><p>Run scenarios side by side — instantly see<br>impacts.</p></div>

<div class="btn" style="left:449px;top:2448px;width:302px;height:44px;font-size:14px;justify-content:flex-start;padding-left:24px">Request A Technical Walkthrough
  <span class="arrow" style="position:absolute;right:8px"><svg width="14" height="14" viewBox="0 0 14 14"><path d="M2 7h10M8 3l4 4-4 4" fill="none" stroke="#0054AA" stroke-width="1.6"/></svg></span></div>

<!-- Latest insights -->
<section class="abs band-tint" style="top:2575px;height:684px"></section>
<h2 class="section-title" style="top:2646px">LATEST <span>INSIGHTS</span></h2>

<article class="insight" style="left:142px">
  <div class="thumb" role="img" aria-label="Photo of a person working with a laptop and calculator at a desk" style="background:linear-gradient(135deg,#dfe8f2,#9fb4ca 55%,#6b8099)"></div>
  <h3>Advancing Actuarial Methods in a Changing Regulatory Landscape</h3>
  <p>Exploring how modern tools support evolving best practices in reserving and capital modeling.</p>
  <div class="learn" style="left:19px;top:334px">Learn More <svg width="16" height="10" viewBox="0 0 16 10"><path d="M1 5h13M10 1l4 4-4 4" fill="none" stroke="#EE7325" stroke-width="1.4"/></svg></div>
</article>
<article class="insight" style="left:457px">
  <div class="thumb" role="img" aria-label="Photo of printed charts and a laptop on a warm-toned desk" style="background:linear-gradient(135deg,#f7d2b0,#eea56e 50%,#cf8a52)"></div>
  <h3>Governance and Documentation in Actuarial Modeling</h3>
  <p>Why audit trails and assumption transparency are critical for internal and external review.</p>
  <div class="learn" style="left:19px;top:334px">Learn More <svg width="16" height="10" viewBox="0 0 16 10"><path d="M1 5h13M10 1l4 4-4 4" fill="none" stroke="#EE7325" stroke-width="1.4"/></svg></div>
</article>
<article class="insight" style="left:772px">
  <div class="thumb" role="img" aria-label="Photo of colleagues reviewing data on a laptop in an office" style="background:linear-gradient(135deg,#2f4258,#566c84 50%,#223244)"></div>
  <h3>Multi-Jurisdictional Actuarial Practice: Challenges &amp; Solutions</h3>
  <p>Strategies for managing compliance across Solvency II, NAIC, and emerging frameworks.</p>
  <div class="learn" style="left:19px;top:334px">Learn More <svg width="16" height="10" viewBox="0 0 16 10"><path d="M1 5h13M10 1l4 4-4 4" fill="none" stroke="#EE7325" stroke-width="1.4"/></svg></div>
</article>

<div class="btn" style="left:516px;top:3132px;width:168px;height:43px;font-size:14px;justify-content:flex-start;padding-left:24px">Read Insights
  <span class="arrow" style="position:absolute;right:8px"><svg width="14" height="14" viewBox="0 0 14 14"><path d="M2 7h10M8 3l4 4-4 4" fill="none" stroke="#0054AA" stroke-width="1.6"/></svg></span></div>

<!-- Footer band -->
<footer class="abs site-footer">
  <div class="brand"><span class="brand-dot"></span>QP FIDUCIARY</div>
  <p class="footer-about">Software that translates actuarial methodologies into disciplined decision-ready analytical tools across diverse regulatory environments.</p>

  <h4 class="footer-h" style="left:576px">QUICK LINKS</h4>
  <ul class="quick-links">
    <li>Home</li><li>Platform</li><li>Solutions</li><li>Insights</li><li>Company</li><li>Contact</li>
  </ul>

  <h4 class="footer-h" style="left:813px">CONTACT DETAILS</h4>
  <div class="contact-row" style="top:248px">
    <svg width="14" height="18" viewBox="0 0 14 18"><path d="M7 1a6 6 0 016 6c0 4-6 10-6 10S1 11 1 7a6 6 0 016-6z" fill="#fff"/><circle cx="7" cy="7" r="2.2" fill="#0B2A4A"/></svg>
    <div><strong>QP FIDUCIARY, Inc.</strong><br>410 Harbor Crest Ave, Suite 200<br>Bayview, FL 33990</div>
  </div>
  <div class="contact-row" style="top:334px">
    <svg width="14" height="14" viewBox="0 0 14 14"><path d="M3 1l2.5 3-1.5 2a8 8 0 004 4l2-1.5 3 2.5-1.5 2C5 13 1 9 1 2.5z" fill="#fff"/></svg>
    <strong>+1(555)010-4821</strong>
  </div>
  <div class="contact-row" style="top:374px">
    <svg width="15" height="12" viewBox="0 0 15 12"><rect x="0.5" y="0.5" width="14" height="11" fill="#fff"/><path d="M1 1l6.5 5L14 1" fill="none" stroke="#0B2A4A" stroke-width="1.2"/></svg>
    <span>hello@qp-fiduciary.example</span>
  </div>

  <div class="footer-rule"></div>
  <p class="copyright">© 2026 QP Fiduciary. All rights reserved. &nbsp;&nbsp;&nbsp;&nbsp;&nbsp;&nbsp; Privacy · Terms</p>
  <span class="social" style="left:948px" aria-label="Social profile"></span>
  <span class="social" style="left:987px" aria-label="Social profile"></span>
  <span class="social" style="left:1026px" aria-label="Social profile"></span>
</footer>

<!-- Call to action -->
<section class="abs cta" role="img" aria-label="Dark photo of a hand holding a smartphone with a glowing digital globe">
  <h2>READY TO SEE THE<br>PLATFORM IN ACTION?</h2>
  <p>Schedule a technical walkthrough and discover how QP Fiduciary can bring<br>structure, transparency, and auditability to your actuarial processes.</p>
  <div class="btn" style="left:307px;top:246px;width:302px;height:44px;font-size:14px;justify-content:flex-start;padding-left:24px;background:var(--sky)">Request A Technical Walkthrough
    <span class="arrow" style="position:absolute;right:8px"><svg width="14" height="14" viewBox="0 0 14 14"><path d="M2 7h10M8 3l4 4-4 4" fill="none" stroke="#0094D4" stroke-width="1.6"/></svg></span></div>
</section>

</body>
</html>
```